Dental office stationary (letterhead, envelopes), business cards, presentation folders

Nothing too dental outside of the logo. I will need all stationary, presentation folders, business cards. Would prefer to stay in the colors of the logo

Gordon Patel, DDS
Bright Haven Dental Implant Center
555-318-2790
info@brighthavendental.example
4817 NW Maple Crest Rd Unit B
Harbor Vale, ST 00000

Also need appointment date and time
And cancellation policy
I want it to say “kindly ask for
A 48hr cancellation policy to avoid incurring a cancellation fee”

Industry/Entity Type

Dental

Colors
0054AA
0677BA
7BADD7
CADEEF
E8F1F8

Requirements
Must have
• Name of your office, name of doctor, address, phone number
Should not have
• Too much tooth/dental. Only the tooth in logo

```html
<!DOCTYPE html>
<html lang="en">
<head>
<meta charset="utf-8">
<title>Bright Haven Dental Implant Center – Business Card</title>
<link href="https://fonts.googleapis.com/css2?family=Marcellus&family=Arimo:wght@400&display=swap" rel="stylesheet">
<style>
  :root {
    --stage: #3d3d3d;
    --card-light: #ffffff;
    --card-dark: #2e2e2e;
    --navy: #0054AA;
    --blue: #0677BA;
    --teal: #1fb39a;
    --ink: #2a2a2a;
    --edge: #d9d9d9;
  }
  * { margin: 0; padding: 0; box-sizing: border-box; }
  html, body { width: 1200px; height: 803px; overflow: hidden; background: var(--stage); }
  .stage {
    position: relative; width: 1200px; height: 803px;
    display: flex; align-items: center; justify-content: center; gap: 60px;
  }
  .card {
    width: 510px; height: 292px; border-radius: 18px; position: relative;
    box-shadow: 0 14px 30px rgba(0,0,0,0.35);
  }
  .card--front {
    background: var(--card-light); padding: 34px 40px 30px;
    display: flex; flex-direction: column; justify-content: flex-end;
  }
  .card--back {
    background: var(--card-dark); border: 1.5px solid var(--edge);
    display: flex; align-items: center; justify-content: center;
  }

  .brand {
    font-family: "Marcellus", serif; font-weight: 400; color: var(--blue);
    line-height: 1.15; white-space: nowrap;
  }
  .brand--small { font-size: 17px; }
  .brand--large { font-size: 27px; }

  .doctor { margin-top: 16px; font-family: "Marcellus", serif; }
  .doctor__name { font-size: 21px; color: var(--navy); letter-spacing: 0.5px; text-transform: uppercase; line-height: 1.1; }
  .doctor__title { font-family: "Arimo", sans-serif; font-size: 12px; color: var(--teal); margin-top: 3px; }

  .address { margin-top: 14px; font-family: "Arimo", sans-serif; font-size: 12.5px; color: var(--ink); line-height: 1.4; }

  .contacts { list-style: none; margin-top: 10px; font-family: "Arimo", sans-serif; font-size: 12.5px; color: var(--ink); }
  .contacts li { display: flex; align-items: center; gap: 8px; line-height: 1.55; }
  .contacts svg { width: 11px; height: 11px; fill: var(--blue); flex: none; }
</style>
</head>
<body>
<main class="stage">
  <section class="card card--front">
    <div class="brand brand--small">Bright Haven Dental Implant Center</div>
    <div class="doctor">
      <div class="doctor__name">Gordon Patel</div>
      <div class="doctor__title">DDS</div>
    </div>
    <p class="address">4817 NW Maple Crest Rd Unit B<br>Harbor Vale, ST 00000</p>
    <ul class="contacts">
      <li><svg viewBox="0 0 12 12" aria-hidden="true"><path d="M2.5 1h2l1 3-1.3.9a6.5 6.5 0 0 0 3 3L8 6.5l3 1v2A1.5 1.5 0 0 1 9.5 11C5 11 1 7 1 2.5A1.5 1.5 0 0 1 2.5 1z"/></svg>555-318-2790</li>
      <li><svg viewBox="0 0 12 12" aria-hidden="true"><path d="M1 2.5h10v7H1z M1 2.5l5 4 5-4" fill="none" stroke="#0677BA" stroke-width="1.2"/></svg>info@brighthavendental.example</li>
      <li><svg viewBox="0 0 12 12" aria-hidden="true"><circle cx="6" cy="6" r="5"/></svg>www.brighthavendental.example</li>
    </ul>
  </section>

  <section class="card card--back">
    <div class="brand brand--large">Bright Haven Dental Implant Center</div>
  </section>
</main>
</body>
</html>
```